Velundra Jobs portal

Velundra Jobs is a job portal connecting job seekers and companies offering part time jobs in the Mena region, starting in the UAE. We would like to see designs that use the color blue. We have attached images to give an idea what the website should look like. When a company posts a job the job seekers are not allowed to see which company has posted a job. There should also be a coinvex gateway. On the landing page we want a catching picture that we will send.

Target Market(s)

Students and promotional workers

Logo Text

Velundra Jobs

Coding

Coded - Design and coding required

Number of Pages Required

4 page

Font styles to use
Sans Serif

Colors
33a6d7
0692cd
85cae6

```html
<!DOCTYPE html>
<html lang="en">
<head>
<meta charset="utf-8">
<title>Velundra Jobs – Professional</title>
<link href="https://fonts.googleapis.com/css2?family=Open+Sans:wght@400;600&family=Arimo:wght@400&display=swap" rel="stylesheet">
<style>
  :root {
    --sidebar: #272727;
    --sidebar-text: #b9bcc2;
    --sidebar-line: #3a3a3a;
    --topbar: #343946;
    --topbar-text: #8b909c;
    --accent: #1c9fe6;
    --navy: #15305e;
    --row-light: #9db3cb;
    --row-light-end: #88b3d3;
    --select: #a1b2ca;
    --logo: #4aa3ad;
    --ink: #1c2431;
    --white: #ffffff;
  }
  * { box-sizing: border-box; margin: 0; padding: 0; }
  html, body { width: 1200px; height: 853px; overflow: hidden; background: var(--white); }
  body { position: relative; font-family: "Open Sans", sans-serif; }

  .sidebar { position: absolute; left: 0; top: 0; width: 175px; height: 853px; background: var(--sidebar); }
  .brand { position: absolute; top: 28px; left: 0; width: 175px; text-align: center; color: var(--logo); font-size: 31px; font-weight: 400; letter-spacing: -0.5px; }
  .nav { position: absolute; top: 96px; left: 0; width: 175px; list-style: none; }
  .nav li { height: 33px; display: flex; align-items: center; padding-left: 18px; font-size: 11px; color: var(--sidebar-text); }
  .nav li svg { width: 12px; height: 12px; margin-right: 10px; fill: var(--sidebar-text); }
  .nav li.active { background: var(--accent); color: var(--white); }
  .nav li.active svg { fill: var(--white); }
  .nav-rule { position: absolute; top: 305px; left: 0; width: 175px; height: 3px; border-top: 1px solid #1f1f1f; border-bottom: 1px solid var(--sidebar-line); }
  .side-foot { position: absolute; left: 24px; width: 150px; font-size: 9.5px; line-height: 16px; color: #9a9da3; white-space: nowrap; }
  .side-links { top: 685px; }
  .side-rule { position: absolute; top: 728px; left: 24px; width: 140px; border-top: 1px solid var(--sidebar-line); }
  .side-copy { top: 740px; font-size: 9px; }

  .topbar { position: absolute; left: 175px; top: 0; width: 1025px; height: 44px; background: var(--topbar); }
  .top-links { position: absolute; left: 20px; top: 11px; font-size: 15px; color: var(--topbar-text); display: flex; align-items: center; }
  .top-links .dot { width: 4px; height: 4px; border-radius: 50%; background: #4d5260; margin: 0 10px 0 14px; }
  .icon-search { position: absolute; left: 635px; top: 13px; }
  .icon-bell { position: absolute; left: 673px; top: 12px; }
  .badge { position: absolute; left: 687px; top: 6px; width: 14px; height: 14px; border-radius: 50%; background: #e8202f; color: var(--white); font-size: 8px; text-align: center; line-height: 14px; font-family: Arimo, sans-serif; }
  .user { position: absolute; left: 731px; top: 0; width: 201px; height: 44px; background: var(--accent); }
  .avatar { position: absolute; left: 15px; top: 4px; width: 37px; height: 37px; border-radius: 50%; background: linear-gradient(160deg, #d9dde2, #6f7884); border: 2px solid var(--white); }
  .user-name { position: absolute; left: 67px; top: 13px; color: var(--white); font-family: Arimo, sans-serif; font-size: 16px; white-space: nowrap; }
  .user-caret { position: absolute; left: 158px; top: 17px; }

  .filter { position: absolute; left: 235px; top: 85px; width: 870px; height: 45px; background: var(--navy); border-radius: 6px; }
  .select { position: absolute; top: 8px; height: 30px; width: 222px; background: var(--select); border-radius: 2px; font-family: Arimo, sans-serif; font-size: 11px; color: var(--ink); padding-left: 19px; line-height: 30px; }
  .select::after { content: ""; position: absolute; right: 14px; top: 12px; border-left: 5px solid transparent; border-right: 5px solid transparent; border-top: 6px solid var(--navy); }
  .search-btn { position: absolute; left: 751px; top: 8px; width: 112px; height: 30px; background: var(--accent); color: var(--white); font-family: Arimo, sans-serif; font-size: 11.5px; text-align: center; line-height: 30px; }

  .jobs { position: absolute; left: 236px; top: 169px; width: 870px; border-collapse: collapse; font-family: Arimo, sans-serif; }
  .jobs th { height: 57px; background: var(--navy); color: var(--white); font-weight: 400; font-size: 15px; }
  .jobs td { height: 45.5px; font-size: 13px; text-align: center; border-top: 3px solid var(--accent); }
  .jobs .light td { background: var(--row-light); color: #eef3f8; }
  .jobs .dark td { background: var(--navy); color: var(--white); }
  .jobs tr:last-child td { border-bottom: 3px solid var(--accent); background: var(--row-light-end); }
  .col-title { width: 198px; } .col-date { width: 242px; } .col-provider { width: 204px; }
  .apply { display: inline-block; width: 111px; height: 30px; line-height: 30px; background: var(--accent); color: var(--white); font-size: 12.5px; margin-left: 66px; }

  .featured-title { position: absolute; left: 235px; top: 590px; font-size: 18px; font-weight: 400; color: var(--ink); }
  .featured-rule { position: absolute; left: 237px; top: 630px; width: 870px; border-top: 1px dashed #222; }
  .providers { position: absolute; left: 236px; top: 653px; display: flex; gap: 21px; }
  .provider-photo { width: 201px; height: 121px; border: 1px solid #cfd4da; box-shadow: 0 1px 3px rgba(0,0,0,.25); }
  .p1 { background: linear-gradient(135deg, #c9d4dc, #253650); }
  .p2 { background: linear-gradient(135deg, #8a949f, #2c3b58 70%, #d5dbe0); }
  .p3 { background: linear-gradient(135deg, #dce3ea, #3a4a66 60%, #e7ecf0); }
  .p4 { background: linear-gradient(135deg, #b7c7d4, #2e3645 60%, #e3e9ee); }
</style>
</head>
<body>
  <aside class="sidebar">
    <div class="brand">velundra</div>
    <ul class="nav">
      <li><svg viewBox="0 0 12 12"><path d="M3 1h8l-2 10H1z"/></svg>It Services</li>
      <li class="active"><svg viewBox="0 0 12 12"><circle cx="6" cy="6" r="5.5"/></svg>Professional</li>
      <li><svg viewBox="0 0 12 12"><path d="M2 0h6l3 3v9H2z"/></svg>Technicians</li>
      <li><svg viewBox="0 0 12 12"><path d="M6 0l1.8 4 4.2.3-3.2 2.8 1 4.2L6 9 2.2 11.3l1-4.2L0 4.3 4.2 4z"/></svg>Sales workers</li>
      <li><svg viewBox="0 0 12 12"><rect x="0" y="1" width="12" height="2.5"/><rect x="0" y="5" width="12" height="2.5"/><rect x="0" y="9" width="12" height="2.5"/></svg>Operatives</li>
      <li><svg viewBox="0 0 12 12"><path d="M6 0a6 6 0 110 12A6 6 0 016 0zm0 2a4 4 0 100 8 4 4 0 000-8zm0 2a2 2 0 110 4 2 2 0 010-4z"/></svg>Services Workrs</li>
    </ul>
    <div class="nav-rule"></div>
    <div class="side-foot side-links">Aboutus Terms and Condition<br>Sitemap</div>
    <div class="side-rule"></div>
    <div class="side-foot side-copy">Copyright © 2015 Velundra, Inc.<br>All rights reserved.</div>
  </aside>

  <header class="topbar">
    <nav class="top-links"><span>About us</span><span class="dot"></span><span>Contact us</span></nav>
    <svg class="icon-search" width="20" height="20" viewBox="0 0 20 20"><circle cx="8" cy="8" r="6" fill="none" stroke="#1c9fe6" stroke-width="2.6"/><path d="M12.5 12.5l5 5" stroke="#1c9fe6" stroke-width="3" stroke-linecap="round"/></svg>
    <svg class="icon-bell" width="20" height="22" viewBox="0 0 20 22"><path d="M10 2c-3.5 0-5.5 2.6-5.5 6v4.5L2.5 16h15l-2-3.5V8C15.5 4.6 13.5 2 10 2z" fill="none" stroke="#1c9fe6" stroke-width="2"/><path d="M7.5 18a2.5 2.5 0 005 0" fill="none" stroke="#1c9fe6" stroke-width="2"/></svg>
    <span class="badge">3</span>
    <div class="user">
      <div class="avatar" role="img" aria-label="User profile photo"></div>
      <span class="user-name">Omar Said</span>
      <svg class="user-caret" width="15" height="15" viewBox="0 0 15 15"><circle cx="7.5" cy="7.5" r="7.5" fill="#fff"/><path d="M4.3 6l3.2 3.2L10.7 6" fill="none" stroke="#1c9fe6" stroke-width="2"/></svg>
    </div>
  </header>

  <form class="filter">
    <div class="select" style="left:8px">Types of work offered</div>
    <div class="select" style="left:247px">Location</div>
    <div class="select" style="left:489px">Language Known</div>
    <div class="search-btn">Search</div>
  </form>

  <table class="jobs">
    <thead><tr><th class="col-title">Job Title</th><th class="col-date">Due Date</th><th class="col-provider">Provider Name</th><th></th></tr></thead>
    <tbody>
      <tr class="light"><td>Job Title Number 1</td><td>25 May 2015</td><td>Provider 1</td><td><span class="apply">Apply Now</span></td></tr>
      <tr class="dark"><td>Job Title Number 1</td><td>25 May 2015</td><td>Provider 1</td><td><span class="apply">Apply Now</span></td></tr>
      <tr class="light"><td>Job Title Number 1</td><td>25 May 2015</td><td>Provider 1</td><td><span class="apply">Apply Now</span></td></tr>
      <tr class="dark"><td>Job Title Number 1</td><td>25 May 2015</td><td>Provider 1</td><td><span class="apply">Apply Now</span></td></tr>
      <tr class="light"><td>Job Title Number 1</td><td>25 May 2015</td><td>Provider 1</td><td><span class="apply">Apply Now</span></td></tr>
      <tr class="dark"><td>Job Title Number 1</td><td>25 May 2015</td><td>Provider 1</td><td><span class="apply">Apply Now</span></td></tr>
      <tr class="light"><td>Job Title Number 1</td><td>25 May 2015</td><td>Provider 1</td><td><span class="apply">Apply Now</span></td></tr>
    </tbody>
  </table>

  <h2 class="featured-title">Featured Job Providers</h2>
  <div class="featured-rule"></div>
  <div class="providers">
    <div class="provider-photo p1" role="img" aria-label="Two business people shaking hands in an office"></div>
    <div class="provider-photo p2" role="img" aria-label="Smiling businesswoman at a meeting table"></div>
    <div class="provider-photo p3" role="img" aria-label="Colleagues discussing work at a desk"></div>
    <div class="provider-photo p4" role="img" aria-label="Team meeting in a bright conference room"></div>
  </div>
</body>
</html>
```